Real Estate Brokerage Stationery Designs

I am looking to have presentation folders with business card slots on both sides along with pockets on both sides. I've attached logos, website colors along with current business card designs.

I am looking for envelope designs both big and small. Possibly new business card designs, notepad templates for big and small notepads. Letterhead designs. Pop socket designs. Realtors name badge designs.

www.brightholdrealty.example

```html
<!DOCTYPE html>
<html lang="en">
<head>
<meta charset="utf-8">
<title>Brighthold Realty Stationery</title>
<link rel="stylesheet" href="https://fonts.googleapis.com/css2?family=Open+Sans:wght@400;600&family=Tinos&display=swap">
<style>
:root{
  --backdrop:#aaa9aa;
  --brand-blue:#0055a5;
  --paper-light:#f7f7f7;
  --paper-dark:#e2e2e2;
  --ink:#4a4a4a;
  --ink-soft:#555;
  --white:#ffffff;
}
*{margin:0;padding:0;box-sizing:border-box}
html,body{width:1200px;height:871px;overflow:hidden;background:var(--backdrop)}
.canvas{position:relative;width:1200px;height:871px}
.paper{position:absolute;background:linear-gradient(90deg,var(--paper-light),var(--paper-dark));box-shadow:0 1px 3px rgba(0,0,0,.35)}

/* envelope front */
.envelope-front{left:54px;top:216px;width:560px;height:254px}
.envelope-front .brand-name{position:absolute;left:32px;top:88px;width:110px;text-align:center;font:600 15px/1.1 "Open Sans",sans-serif;color:var(--brand-blue)}
.envelope-front .return-address{position:absolute;left:26px;top:124px;width:122px;text-align:center;font:400 7px/9.6px "Open Sans",sans-serif;color:var(--ink-soft)}
.envelope-front .base-band{position:absolute;left:0;bottom:0;width:100%;height:8px;background:var(--brand-blue)}

/* envelope back */
.envelope-back{left:54px;top:500px;width:560px;height:254px}
.envelope-back .flap{position:absolute;left:0;top:0}
.envelope-back .flap-name{position:absolute;left:0;top:40px;width:100%;text-align:center;font:600 15px/1 "Open Sans",sans-serif;color:var(--white)}

/* letterhead */
.letterhead{left:638px;top:57px;width:522px;height:735px}
.letterhead .brand-name{position:absolute;left:0;top:108px;width:100%;text-align:center;font:600 20px/1 "Open Sans",sans-serif;color:var(--brand-blue)}
.letter{position:absolute;left:49px;width:431px;font-family:"Tinos",serif;color:var(--ink)}
.letter-date{top:180px;font-size:9.5px}
.letter-recipient{top:216px;font-size:9.5px;line-height:12px}
.letter-body{top:284px;font-size:7.6px;line-height:12px;text-align:justify}
.letter-body p{margin-bottom:12px}
.signature{position:absolute;left:53px;top:528px;width:106px;height:46px;background:linear-gradient(90deg,#dcdcdc,#d2d2d2);border-radius:3px}
.letter-footer{position:absolute;left:0;top:661px;width:100%;height:55px;background:var(--brand-blue);color:var(--white);font:400 7px/10.2px "Open Sans",sans-serif}
.contact-list{position:absolute;left:63px;top:9px;list-style:none}
.contact-list li{display:flex;align-items:center;gap:5px}
.contact-list svg{width:7px;height:7px;fill:var(--white)}
.footer-address{position:absolute;right:53px;top:15px;text-align:right}
</style>
</head>
<body>
<div class="canvas">

  <section class="paper envelope-front">
    <div class="brand-name">Brighthold Realty</div>
    <div class="return-address">2200 Harbor Point Dr, Suite 410,<br>Lakeview, FL 33010</div>
    <div class="base-band"></div>
  </section>

  <section class="paper envelope-back">
    <svg class="flap" width="560" height="94" viewBox="0 0 560 94">
      <path d="M0 0 H560 L546 64 Q540 94 508 94 H52 Q20 94 14 64 Z" fill="var(--brand-blue)"/>
    </svg>
    <div class="flap-name">Brighthold Realty</div>
  </section>

  <section class="paper letterhead">
    <div class="brand-name">Brighthold Realty</div>
    <div class="letter letter-date">Cartagena de Indias, Ocober 12,2015</div>
    <div class="letter letter-recipient">Sr.<br>MARCO RUIZ<br>Web Master<br>City</div>
    <div class="letter letter-body">
      <p>Contrary to popular belief, Lorem Ipsum is not simply random text. It has roots in a piece of classical Latin literature from 45 BC, making it over 2000 years old. Daniel Whitcombe, a Latin professor at Westbrook College in Virginia, looked up one of the more obscure Latin words, consectetur, from a Lorem Ipsum passage, and going through the cites of the word in classical literature,</p>
      <p>discovered the undoubtable source. Lorem Ipsum comes from sections 1.10.32 and 1.10.33 of "de Finibus Bonorum et Malorum" (The Extremes of Good and Evil) by an ancient author, written in 45 BC. This book is a treatise on the theory of ethics, very popular during the Renaissance. The first line of Lorem Ipsum, "Lorem ipsum dolor sit amet..", comes from a line in section 1.10.32.</p>
      <p>The standard chunk of Lorem Ipsum used since the 1500s is reproduced below for those interested. Sections 1.10.32 and 1.10.33 from "de Finibus Bonorum et Malorum" are also reproduced in their exact original form, accompanied by English versions from the 1914 translation by J. Ellison.</p>
      <p>There are many variations of passages of Lorem Ipsum available, but the majority have suffered alteration in some form, by injected humour, or randomised words which don't look even slightly believable. If you are going to use a passage of Lorem Ipsum, you need to be sure there isn't anything embarrassing hidden in the middle of text.</p>
    </div>
    <div class="signature" role="img" aria-label="Handwritten signature of the sender"></div>
    <footer class="letter-footer">
      <ul class="contact-list">
        <li><svg viewBox="0 0 10 10"><path d="M1 3 Q5 0 9 3 L8 5 L6 4 V3 H4 V4 L2 5 Z M2 6 H8 V9 H2 Z"/></svg>555-014-2210</li>
        <li><svg viewBox="0 0 10 10"><path d="M3 0 H7 V10 H3 Z M4 1 V8 H6 V1 Z"/></svg>555-014-2284</li>
        <li><svg viewBox="0 0 10 10"><path d="M3 1 H7 V4 H3 Z M1 4 H9 V8 H1 Z"/></svg>555-014-2391</li>
        <li><svg viewBox="0 0 10 10"><path d="M0 3 H10 V8 H0 Z"/></svg>info@brightholdrealty.example</li>
      </ul>
      <div class="footer-address">2200 Harbor Point Dr, Suite 410,<br>Lakeview, FL 33010<br>www.brightholdrealty.example</div>
    </footer>
  </section>

</div>
</body>
</html>
```